TalbeckLabs needs a new rocket based website

We need a new website that will be based on our rocket ship logo. We develop innovative solutions for enterprises. We would like to see a design that when the pages scroll, the rocket launches and goes from launch through a journey, similar to how we approach our customer. We would like areas for "Who are we", "What can we do", "What have we done", "How can we help". http://www.talbecklabs.example.au is our current website

Target Market(s)

Government, Enterprise, Cloud

Industry/Entity Type

Software Service

Coding

Coded - Design and coding required

Number of Pages Required

2 page

Requirements
Must have
• We would like to see a design that when the pages scroll, the rocket launches and goes from launch through a journey, similar to how we approach our customer.
• Must have a home page and a detail page.
• Would like to see the logo/rocket animate in some way when you scroll through he page.

```html
<!DOCTYPE html>
<html lang="en">
<head>
<meta charset="utf-8">
<title>TalbeckLabs — Innovative Software Solutions</title>
<link href="https://fonts.googleapis.com/css2?family=Montserrat:wght@600;700&family=Open+Sans:wght@400;600;700&family=Lato:wght@400;700&display=swap" rel="stylesheet">
<style>
:root{
  --orange:#f7821b;
  --orange-dark:#e8730f;
  --hero-grey:#e9e9e9;
  --ink:#111111;
  --text:#5d5d5d;
  --dark:#2a2523;
  --footer:#0f0f0f;
  --white:#ffffff;
  --dot:#3a3a3a;
}
*{margin:0;padding:0;box-sizing:border-box}
html,body{width:1200px;height:2932px;overflow:hidden}
body{position:relative;background:var(--white);font-family:"Open Sans",Arial,sans-serif;color:var(--text)}
.abs{position:absolute}
h1,h2,h3,.brand{font-family:"Montserrat",Arial,sans-serif;color:var(--ink)}
.btn{position:absolute;display:flex;align-items:center;justify-content:center;width:164px;height:44px;border-radius:22px;background:var(--orange);color:var(--white);font:700 14px "Lato",Arial,sans-serif;letter-spacing:.5px;text-decoration:none}

/* hero */
.hero-bg{left:0;top:0;width:1200px;height:640px}
.site-header{left:0;top:0;width:1200px;height:110px}
.brand{left:160px;top:34px;font-size:34px;font-weight:700;display:flex;align-items:center;gap:10px}
.brand-mark{width:14px;height:14px;border-radius:50%;background:var(--orange)}
.main-nav{left:513px;top:40px;display:flex;gap:0}
.main-nav a{font:400 16px "Lato",Arial,sans-serif;color:#222;text-decoration:none;margin-right:42px}
.hero-title{left:162px;top:204px;font-size:38px;line-height:44px;font-weight:700}
.hero-text{left:162px;top:302px;width:440px;font-size:15px;line-height:24px;color:#444}
.hero-art{left:690px;top:135px;width:320px;height:355px;border-radius:12px;background:linear-gradient(135deg,#5b7bd8 0%,#3840b8 50%,#e5e7f0 100%)}
.slider-arrow{top:278px;width:26px;height:48px}

/* who */
.who-art{left:190px;top:720px;width:370px;height:320px;border-radius:14px;background:linear-gradient(160deg,#f4a54c 0%,#ffffff 55%,#5f85c9 100%)}
.who-title{left:640px;top:740px;font-size:33px;font-weight:700}
.who-text{left:646px;top:796px;width:410px;font-size:15px;line-height:25px}
.who-text p+p{margin-top:3px}

/* services */
.services-bg{left:0;top:1100px;width:1200px;height:596px}
.services-title{left:0;top:1300px;width:1200px;text-align:center;color:var(--white);font-size:33px;font-weight:700}
.service{width:238px;height:238px;border-radius:50%;background:var(--white);border:2px solid var(--orange-dark);display:flex;flex-direction:column;align-items:center;padding-top:30px;text-align:center;top:1362px}
.service svg{width:64px;height:64px;margin-bottom:14px}
.service h3{font-size:17px;line-height:20px;font-weight:700;margin-bottom:6px;padding:0 30px}
.service p{font-size:12px;line-height:15px;color:#777;padding:0 40px}
.service.is-active{background:var(--ink)}
.service.is-active h3{color:var(--white)}
.service.is-active p{color:#ddd}

/* work */
.work-title{left:0;top:1800px;width:1200px;text-align:center;font-size:33px;font-weight:700}
.work-photo{width:206px;height:210px}
.project-overlay{display:flex;flex-direction:column;align-items:center;justify-content:center;gap:8px;color:var(--white);font:600 16px "Open Sans",Arial,sans-serif;letter-spacing:.5px}

/* help */
.help-bg{left:0;top:2210px;width:1200px;height:592px}
.help-title{left:162px;top:2420px;font-size:33px;font-weight:700;color:var(--white)}
.help-text{left:162px;top:2476px;width:450px;font-size:15px;line-height:25px;color:#cfcac6}
.help-text p+p{margin-top:3px}
.help-art{left:640px;top:2370px;width:380px;height:340px;border-radius:14px;background:linear-gradient(150deg,#4a3f8f 0%,#c9cbf5 60%,#e4234f 100%)}

/* footer */
.site-footer{left:0;top:2800px;width:1200px;height:132px;background:var(--footer)}
.footer-nav{left:180px;top:38px;display:flex}
.footer-nav a{color:#d8d8d8;font-size:13px;text-decoration:none;margin-right:26px}
.copyright{left:180px;top:70px;font-size:11px;color:#aaa}
.social{left:888px;top:40px;display:flex;gap:28px}
.social span{width:18px;height:18px;border-radius:50%;background:#fff}
</style>
</head>
<body>

<!-- hero background with cloud edge -->
<svg class="abs hero-bg" viewBox="0 0 1200 640" aria-hidden="true">
  <defs><linearGradient id="heroShade" x1="0" y1="0" x2="0" y2="1"><stop offset="0" stop-color="#ebebeb"/><stop offset="1" stop-color="#d9d9d9"/></linearGradient></defs>
  <rect width="1200" height="520" fill="#ebebeb"/>
  <g fill="url(#heroShade)">
    <circle cx="40" cy="540" r="80"/><circle cx="170" cy="555" r="90"/><circle cx="310" cy="530" r="85"/>
    <circle cx="450" cy="550" r="90"/><circle cx="600" cy="560" r="70"/><circle cx="740" cy="540" r="95"/>
    <circle cx="880" cy="555" r="80"/><circle cx="1010" cy="535" r="95"/><circle cx="1150" cy="560" r="80"/>
  </g>
</svg>

<header class="abs site-header">
  <div class="abs brand"><span class="brand-mark"></span>TalbeckLabs</div>
  <nav class="abs main-nav">
    <a href="#">About Us</a><a href="#">Services</a><a href="#">Why We Are</a><a href="#">Our Blogs</a><a href="#">Contact Us</a>
  </nav>
</header>

<svg class="abs slider-arrow" style="left:96px" viewBox="0 0 26 48" aria-label="Previous slide"><path d="M22 2 4 24l18 22" fill="none" stroke="#777" stroke-width="2.5"/></svg>
<svg class="abs slider-arrow" style="left:1076px" viewBox="0 0 26 48" aria-label="Next slide"><path d="M4 2l18 22L4 46" fill="none" stroke="#777" stroke-width="2.5"/></svg>

<h1 class="abs hero-title">We Provide Innovative<br>Software Solutions</h1>
<p class="abs hero-text">Class aptent taciti sociosqu ad litora torquent per conubia nostra per inceptos hymenaeos Proin nulla arcu</p>
<a class="btn" href="#" style="left:162px;top:373px">LEARN MORE</a>
<div class="abs hero-art" role="img" aria-label="Isometric illustration of a web page layout with media and chat icons"></div>

<!-- journey path -->
<svg class="abs" style="left:0;top:0" width="1200" height="2932" viewBox="0 0 1200 2932" aria-hidden="true">
  <g fill="none" stroke="var(--dot)" stroke-width="2" stroke-dasharray="4 5">
    <path d="M608 600V752H630"/>
    <path d="M823 1030V1150H603V1290"/>
    <path d="M598 1696V1772"/>
    <path d="M600 2130V2188H373V2374"/>
  </g>
  <circle cx="608" cy="566" r="12" fill="var(--orange)"/>
  <circle cx="603" cy="1296" r="5" fill="#fff" stroke="var(--dot)" stroke-width="2"/>
  <circle cx="598" cy="1778" r="5" fill="var(--orange)" stroke="var(--dot)" stroke-width="2"/>
</svg>

<!-- who are we -->
<div class="abs who-art" role="img" aria-label="Illustration of a crane building websites on a desktop, tablet and phone with gears"></div>
<h2 class="abs who-title">Who are we</h2>
<div class="abs who-text">
  <p>Aalesuada iaculis ipsum dui aliquet felis at cursus magna nisl nec elit Praesent elementum elit at tellus</p>
  <p>Aultricies sit amet porttitor mattis enim In massa libero interdum nec interdum vel blandit sed nulla In ullam-corper est eget tempor cursus neque mi consectetuer mi a ultricies massa est sed nisl Class aptent taciti</p>
</div>
<a class="btn" href="#" style="left:644px;top:980px">LEARN MORE</a>

<!-- what can we do -->
<svg class="abs services-bg" viewBox="0 0 1200 596" aria-hidden="true">
  <g fill="var(--orange)">
    <rect y="80" width="1200" height="516"/>
    <circle cx="20" cy="110" r="60"/><circle cx="170" cy="90" r="85"/><circle cx="320" cy="115" r="70"/>
    <circle cx="470" cy="90" r="80"/><circle cx="620" cy="110" r="70"/><circle cx="780" cy="95" r="85"/>
    <circle cx="940" cy="115" r="65"/><circle cx="1080" cy="90" r="80"/><circle cx="1190" cy="105" r="60"/>
  </g>
</svg>
<h2 class="abs services-title">What can we do</h2>

<div class="abs service" style="left:157px">
  <svg viewBox="0 0 64 64" aria-hidden="true"><g fill="none" stroke="#222" stroke-width="2"><rect x="10" y="10" width="44" height="44"/><circle cx="32" cy="32" r="12"/><circle cx="32" cy="32" r="5"/><circle cx="10" cy="10" r="4"/><circle cx="54" cy="10" r="4"/><circle cx="10" cy="54" r="4"/><circle cx="54" cy="54" r="4"/></g></svg>
  <h3>e-Parliament</h3>
  <p>All of your Parliamentary software and business process needs.</p>
</div>
<div class="abs service" style="left:368px">
  <svg viewBox="0 0 64 64" aria-hidden="true"><g fill="none" stroke="#222" stroke-width="2"><path d="M18 44H14a10 10 0 0 1 0-20 14 14 0 0 1 27-4 11 11 0 0 1 11 24h-6"/><path d="M32 56V30m-8 8 8-8 8 8"/></g></svg>
  <h3>Cloud</h3>
  <p>Nimbus Office Suite, Migration, Security, Cust-omisations.</p>
</div>
<div class="abs service is-active" style="left:579px">
  <svg viewBox="0 0 64 64" aria-hidden="true"><g fill="none" stroke="var(--orange)" stroke-width="3"><path d="M12 52 48 16l4 4-36 36H12z"/><path d="M52 52 16 16l4-4 36 36v4z"/></g></svg>
  <h3>Architecture and Design</h3>
  <p>Business process design, technology strategy and architecture.</p>
</div>
<div class="abs service" style="left:803px">
  <svg viewBox="0 0 64 64" aria-hidden="true"><g fill="none" stroke="#222" stroke-width="2"><rect x="8" y="8" width="48" height="36" rx="2"/><path d="M8 16h48M20 26h24M20 32h16"/><circle cx="42" cy="48" r="7"/><circle cx="42" cy="48" r="2"/></g></svg>
  <h3>Software Development</h3>
  <p>Software development including business apps, web and mobile.</p>
</div>

<!-- what have we done -->
<h2 class="abs work-title">What have we done</h2>
<div class="abs work-photo" style="left:162px;top:1878px;background:linear-gradient(135deg,#1a2232,#3a5f8c 60%,#c77a2a)" role="img" aria-label="Photo of code on a dark monitor"></div>
<div class="abs work-photo" style="left:386px;top:1916px;background:linear-gradient(135deg,#d8d4cf,#9a8676 55%,#e9e6e2)" role="img" aria-label="Photo of a developer working at a laptop"></div>
<div class="abs work-photo" style="left:608px;top:1876px;background:linear-gradient(135deg,#5a5650,#2f3338 55%,#b3b1ab)" role="img" aria-label="Photo of a team working together at computers"></div>
<div class="abs work-photo project-overlay" style="left:830px;top:1920px;background:linear-gradient(135deg,#2d3640,#141a20)" role="img" aria-label="Photo of hands typing on a keyboard, project thumbnail">
  <span>PROJECT TITLE</span>
  <svg width="30" height="30" viewBox="0 0 30 30" aria-hidden="true"><circle cx="15" cy="15" r="13" fill="none" stroke="#fff" stroke-width="1.5"/><path d="M9 12l6 6 6-6" fill="none" stroke="#fff" stroke-width="1.5"/></svg>
</div>

<!-- how can we help -->
<svg class="abs help-bg" viewBox="0 0 1200 592" aria-hidden="true">
  <g fill="var(--dark)">
    <rect y="70" width="1200" height="522"/>
    <circle cx="30" cy="100" r="70"/><circle cx="180" cy="80" r="80"/><circle cx="340" cy="105" r="70"/>
    <circle cx="500" cy="90" r="85"/><circle cx="660" cy="105" r="70"/><circle cx="820" cy="85" r="80"/>
    <circle cx="980" cy="100" r="70"/><circle cx="1120" cy="80" r="85"/>
  </g>
</svg>
<svg class="abs" style="left:367px;top:2374px" width="12" height="12" aria-hidden="true"><circle cx="6" cy="6" r="5" fill="var(--orange)" stroke="#fff" stroke-width="1.5"/></svg>
<h2 class="abs help-title">How can we help</h2>
<div class="abs help-text">
  <p>Aalesuada iaculis ipsum dui aliquet felis at cursus magna nisl nec elit Praesent elementum elit at tellus</p>
  <p>Aultricies sit amet porttitor mattis enim In massa libero interdum nec interdum vel blandit sed nulla In ullamcorper est eget tempor cursus neque mi consectetuer</p>
</div>
<a class="btn" href="#" style="left:162px;top:2630px">LEARN MORE</a>
<div class="abs help-art" role="img" aria-label="Illustration of a laptop with code windows, a coffee cup and a notebook"></div>

<!-- footer -->
<footer class="abs site-footer">
  <nav class="abs footer-nav">
    <a href="#">Home</a><a href="#">About Us</a><a href="#">Services</a><a href="#">Why We Are</a><a href="#">Our Blogs</a><a href="#">Contact Us</a>
  </nav>
  <p class="abs copyright">© 2018 TalbeckLabs  All right reserved</p>
  <div class="abs social" aria-label="Social links"><span></span><span></span><span></span></div>
</footer>

</body>
</html>
```